Communication and Marketing agency needs a new presentation card

We are a group of communication and marketing agencies specialized in companies that are in the logistics and industrial sector. The head agency is TELVANO Grupo and the group consists of 4 agencies: TELVANO Media, TELVANO Digital, TELVANO Research and DifundeEnPantalla. We hace 4 offices in Spain (Madrid, Barcelona, Valencia and Murcia). We are looking for a clean and attractive design that transmits our experience, brand presence in the market and knowledge to those who receive the card.It has to maintain the colors of the logo that is attached.
Target Market(s)
logistics and industrial sector
Marketing department
Contact Information for Business Card
Clean and attractive design

```html
<!DOCTYPE html>
<html lang="en">
<head>
<meta charset="utf-8">
<title>TELVANO Grupo – Business Card</title>
<link rel="stylesheet" href="https://fonts.googleapis.com/css2?family=Open+Sans:wght@300;400;700&display=swap">
<style>
  :root {
    --backdrop: #c98285;
    --card-dark: #1c1c1c;
    --card-light: #f8f8f7;
    --brand-red: #b0202c;
    --brand-grey: #5e5e5e;
    --ink: #2a2a2a;
    --map-tone: #262626;
  }
  * { margin: 0; padding: 0; box-sizing: border-box; }
  html, body {
    width: 1200px; height: 1200px; overflow: hidden;
    background: var(--backdrop);
    font-family: "Open Sans", Arial, sans-serif;
  }
  .canvas { position: relative; width: 1200px; height: 1200px; }

  .card {
    position: absolute; left: 224px; width: 814px; height: 465px;
    border-radius: 22px; overflow: hidden;
  }
  .card--front { top: 76px; background: var(--card-dark); }
  .card--back { top: 658px; background: var(--card-light); }

  .world-map {
    position: absolute; inset: 0;
    background: radial-gradient(ellipse 70% 60% at 50% 45%, var(--map-tone) 0%, var(--card-dark) 80%);
  }

  .brand-name {
    position: absolute; text-align: right;
    font-weight: 300; line-height: 1;
  }
  .brand-name__main { display: block; letter-spacing: 6px; }
  .brand-name__sub { display: block; }

  .card--front .brand-name {
    right: 152px; top: 150px; color: var(--brand-grey);
  }
  .card--front .brand-name__main { font-size: 96px; }
  .card--front .brand-name__sub { font-size: 62px; margin-top: 10px; }

  .card--back .brand-name {
    right: 48px; top: 56px; color: var(--brand-red);
  }
  .card--back .brand-name__main { font-size: 84px; }
  .card--back .brand-name__sub { font-size: 54px; margin-top: 8px; }

  .person { position: absolute; left: 54px; top: 258px; }
  .person__name { font-size: 25px; font-weight: 700; color: var(--brand-red); line-height: 1.2; }
  .person__role { font-size: 18px; color: var(--ink); margin-top: 4px; }

  .divider {
    position: absolute; left: 54px; right: 48px; top: 326px;
    height: 1px; background: var(--brand-red);
  }
  .divider::before {
    content: ""; position: absolute; left: 0; top: -1px;
    width: 213px; height: 3px; background: var(--brand-red);
  }

  .contact-list { position: absolute; left: 54px; top: 345px; list-style: none; }
  .contact-list li {
    display: flex; align-items: center; gap: 8px;
    font-size: 18px; color: var(--ink); height: 23.5px;
  }
  .contact-list svg { width: 15px; height: 15px; flex: none; }

  .address {
    position: absolute; right: 48px; top: 368px; text-align: right;
    font-size: 18px; line-height: 23.5px; color: var(--ink); font-style: normal;
  }
</style>
</head>
<body>
<div class="canvas">

  <section class="card card--front">
    <div class="world-map" role="img" aria-label="Faint world map texture across the dark card"></div>
    <div class="brand-name">
      <span class="brand-name__main">TELVANO</span>
      <span class="brand-name__sub">Digital</span>
    </div>
  </section>

  <section class="card card--back">
    <div class="brand-name">
      <span class="brand-name__main">TELVANO</span>
      <span class="brand-name__sub">Grupo</span>
    </div>

    <div class="person">
      <p class="person__name">Marta Velasco</p>
      <p class="person__role">Manager</p>
    </div>

    <div class="divider"></div>

    <ul class="contact-list">
      <li>
        <svg viewBox="0 0 16 16" aria-hidden="true"><path fill="var(--brand-red)" d="M4 1.5 6.2 4 5 5.6c.6 1.8 1.8 3.3 3.4 4.4L10 8.8l2.5 2.2-1.3 2.6C6.5 13 2.6 8.8 2 4.2z"/><path d="M11 4a3 3 0 0 1 1.5 2.6M12.3 2.4A5 5 0 0 1 14.5 6.6" stroke="var(--brand-red)" stroke-width="1.3" fill="none"/></svg>
        +34 -610- 4427
      </li>
      <li>
        <svg viewBox="0 0 16 16" aria-hidden="true"><rect x="1" y="3" width="14" height="10" fill="var(--brand-red)"/><path d="M1.5 3.5 8 9l6.5-5.5M1.5 12.5 6 7.5M14.5 12.5 10 7.5" stroke="#fff" stroke-width="1" fill="none"/></svg>
        info@telvanogrupo.es
      </li>
      <li>
        <svg viewBox="0 0 16 16" aria-hidden="true"><g stroke="var(--brand-red)" stroke-width="1.1" fill="none"><circle cx="8" cy="8" r="6.5"/><ellipse cx="8" cy="8" rx="3" ry="6.5"/><path d="M1.5 8h13M2.5 4.8h11M2.5 11.2h11"/></g></svg>
        www.telvanogrupo.es
      </li>
    </ul>

    <address class="address">
      #204 – 1870 42ND Calle Norte<br>
      Valdemar MD 28014 SPAIN
    </address>
  </section>

</div>
</body>
</html>
```